SaaS / Consulting / Solution website redesign

We need a website design that:
- Is completely different than our current design : https://plumvessel.net
- Has a very minimal amount of copy
- Changes our positioning from a SaaS application to a solutions company. Solutions company means that we help our customers solve their problems with consulting, training, and tools. An example of a solutions company is here: https://oldpages.example/web/20130111103320/http://www.brindlework.com:80/
- Does not make us look like a start up
- Is more people oriented than technology oriented

We need a designer that:
- Is a rebel at heart
- Is a minimalist
- Tells us why our current site sucks
- Can disagree with us
- Can also do copywriting or already has a copywriter that can help
- Is ok with saying we have capability that we don't in order to see if people actually want that
- Can understand the difference between our grand vision and where we need to focus ourselves today in order to get there

Who we are:
- Entrepreneurs
- Programmers
- Consultants
- Investors

Here's our design goals:
#1 Get customers, investors, employers, and partners excited about our unique and clearly articulated value proposition
#2 Get people to contact us asking for help with their programs
#3 Position ourselves as an expert in the skills based volunteering, mentorship, and group collaboration
#4 Make it easy for people, who already know who we are, to register online

What our grand vision is:
- Create a marketplace where any person can go to our site and find time with anyone they need to meet with. Whether that is their hair stylist, school advisor, parent of your kids class, dentist, attorney, etc.

What will you get if you win:
- In addition to the prize of this project we will have many landing pages and other revisions we will need in the future. We currently don't have a designer or copywriter and need to add that capability to our team

Who do we need to appeal to:
- Directors that are launching innovative programs inside organizations
- IT personnel who are trying to disqualify our technology so they don't have to support it or deal with it when it doesn't go well
- Enterprise IT architects who don't want our product being on its own island within their organization totally incompatible with everything else. Architects which are trying to assess how our platform will co-exist with all their other platforms
- Vice Presidents who want to help their directors understand that we don't have enough experience to help them
- Program managers who have to juggle a million things and need a tool that actually helps instead of confuses them and adds more work for them.
- Program managers & directors that have been given ambiguous goals by their board of directors like "improve retention, increase engagement, create innovation, get people to collaborate." And who have no idea where to start or how to deliver on things like that.
- Program managers, directors, and vice presidents that are trying to understand how our technology and services fit into their existing technology and capability
- Employees who are bored and uninspired with their current tools and are hoping for some excitement in their life. Kind of like candy or a double espresso.
- Investors who think, our company like all the rest, are going to waste their money and make them look like a fool

Other information:
-The CSS and html needs to be responsive

-Our registration onboarding flow needs to collect this information:
User first name
user last name
user email
(verify their email)
user phone number
(verify their phone number)
User profile image (optional)
User profile summary (optional, like a bio, freeform text fiels)
If applicable: Register their organization
Organization name
Organization image (optional)
Account Mailing address
account Billing address (could be same as mailing address)
account Billing email address (could be same as user address)
account Product selection (pricing tier)
account Credit card information

The designs I am getting are a good start but they are only the front page. I just want you to know that I am expecting and need more than a landing page to complete the design. I will likely need a page that outlines the benefits and features of the product itself, how its different than our competitors, which will not be on the front page. I will need a registration flow. I will need a blog page design so we can post blog articles, I will need a team page, a page that goes into detail on our training, our services. I will likely need a page that shows all news and media we have been in. I need to show customer and user quotes, case studies, a way to contact us, partners, general resources like on collaboration, product tutorials, customers. I need the site to address a comprehensive set of needs. I need that design to be consistent and thorough. I know what PlateHarbor is. I'm not using because I need more than a template that was customized. I need to be unique and match our brand thoughtfully, beautifully, and artistically. Someone asked me a question about how Murmly is similar to our tool in the way it is referred by end users and purchased by managers. Our website needs to primarily talk to the managers as I explained in the brief but it needs to appear cool and exciting to our end-users without focusing on the technology too much. Murmly is a tool that teams use to collaborate in small and large enterprises. The value prop for them is that communication is easier. But they don't put that on their website. Why? Because the users of the technology won't go to the website to find out information on it, they get their information from someone who is using it and demos it to them. When Ines tells her manager Otto "Lets get murmly, Ruth is using it at her company and its great" Ines's manager doesn't know anything about murmly so she promptly googles it. The most important thing from Ines's perspective is that Otto agrees to try it out. Otto's biggest concern is that productivity will be enhanced to degraded. Murmly knows this and so on the front page they know they are talking to Otto NOT Ines because Ines is already sold on it and doesn't need to get sold on the website. Ines is end user. Otto is the purchaser. We have the same problem and so our end users are not the ones purchasing our product, their managers are purchasing our product. We get referred by our end users and vetted by their managers. Hope this helps! Thank you for looking at this project!  Added Wednesday, June 7, 2017

Another observation I am having about the designs being submitted. I believe we used the animations on our current website because animations / cartoons connect with the "inner child" in our users. Whatever that means :-). I think it's what makes our brand fun. I have a hard time imagining that we could make the design fun looking without animations but I'm sure it can be achieved. I also recognize that blending pictures of real people and animations is hard. So either we must masterfully blend them, use only animations, or make the real people have a LOT of fun! So far most of the designs while achieve the goal of appealing to the serious Vice Presidents and directors, they are not doing a good job at appealing to the overworked program managers and bored employees. There seems to stand another challenge with animations which is animations are hard to find and/or create that achieve the message / emotion we are trying to communicate. I don't have any good answers for this but I will say we can hire both animators and illustrators if we need to. All you have to do is communicate the effect in the website design with some simpler version maybe not the end illustration or animation itself. Added Wednesday, June 7, 2017

• Sex appeal and a sense of humor. Copy that makes people excited and clairvoyant about our potential.
• Boring renditions of other non-inspiring websites

```html
<!DOCTYPE html>
<html lang="en">
<head>
<meta charset="utf-8">
<title>Team – Plumvessel</title>
<link href="https://fonts.googleapis.com/css2?family=Roboto:wght@300;400;500;700&display=swap" rel="stylesheet">
<style>
:root{
  --blue:#29abe2;
  --blue-dark:#1e96c9;
  --green:#8cc63f;
  --ink:#333;
  --muted:#888;
  --light:#eaeaea;
  --footer:#ededed;
  --line:#dcdcdc;
  --white:#fff;
}
*{box-sizing:border-box;margin:0;padding:0}
html,body{width:1200px;height:2344px;overflow:hidden}
body{font-family:'Roboto',sans-serif;color:var(--ink);background:var(--white);position:relative}
.site-header{height:112px;display:flex;align-items:center;justify-content:space-between;padding:0 120px 0 160px}
.brand{display:flex;align-items:center;gap:10px;font-size:26px;font-weight:500;color:var(--blue)}
.brand-dot{width:34px;height:34px;border-radius:50%;background:var(--green)}
.main-nav{display:flex;align-items:center;gap:30px;font-size:13px;color:var(--muted)}
.main-nav .active{color:var(--blue)}
.btn{display:inline-block;padding:10px 20px;font-size:12px;font-weight:500;color:var(--white);border-radius:2px;text-transform:uppercase;letter-spacing:.5px}
.btn-green{background:var(--green)}
.btn-blue{background:var(--blue)}
.hero{height:200px;background:linear-gradient(90deg,var(--blue-dark),var(--blue));display:flex;align-items:center;padding-left:190px;gap:22px;color:var(--white)}
.hero h1{font-size:60px;font-weight:400;letter-spacing:2px}
.crumbs{height:48px;display:flex;align-items:center;justify-content:space-between;padding:0 160px;border-bottom:1px solid var(--line);font-size:12px;color:var(--muted)}
.search{width:200px;height:26px;border:1px solid var(--line);display:flex;align-items:center;justify-content:space-between;padding:0 8px;font-size:11px}
.section{text-align:center}
.section h2{font-size:46px;font-weight:400;letter-spacing:1px;color:var(--ink)}
.founders{height:420px;padding-top:48px}
.members{height:540px;padding-top:50px;background:var(--light)}
.advisors{height:452px;padding-top:68px}
.leads{display:flex;justify-content:center;gap:130px;margin-top:58px}
.lead{display:flex;align-items:center;gap:36px;text-align:left;width:380px}
.avatar{width:120px;height:120px;border-radius:50%;background:radial-gradient(circle at 50% 40%,#bfe6f7,#7fcdee);flex:none}
.lead h3{font-size:14px;font-weight:500;margin-bottom:6px}
.lead p{font-size:11px;line-height:1.5;color:var(--muted);width:210px}
.social{display:flex;gap:8px;margin-top:10px}
.social span{width:10px;height:10px;border-radius:50%;background:#9a9a9a}
.crew{display:grid;grid-template-columns:repeat(4,180px);justify-content:center;gap:26px 60px;margin-top:58px}
.crew.three{grid-template-columns:repeat(3,180px);gap:0 70px;margin-top:44px}
.crew.two{grid-template-columns:repeat(2,180px);gap:0 70px;margin-top:44px}
.mate{display:flex;align-items:center;gap:14px;text-align:left}
.mate .avatar{width:50px;height:50px;background:var(--blue)}
.mate h4{font-size:13px;font-weight:400}
.mate .social{margin-top:5px;gap:6px}
.mate .social span{width:8px;height:8px}
.rule{width:880px;height:1px;background:var(--line);margin:0 auto}
.clients{height:260px;text-align:center;padding-top:60px}
.clients h2{font-size:24px;font-weight:400;letter-spacing:2px;color:#555}
.client-row{display:flex;justify-content:center;align-items:center;gap:38px;margin-top:58px;font-size:15px;font-weight:500;color:#2b4a7a}
.site-footer{position:absolute;left:0;top:2032px;width:1200px;height:312px;background:var(--footer);padding:56px 160px 0}
.foot-top{display:flex;justify-content:space-between}
.foot-about p{font-size:11px;color:var(--muted);line-height:1.6;width:380px;margin:14px 0 22px}
.foot-about .btn{margin-right:8px;font-size:10px;padding:8px 14px}
.btn-outline{background:transparent;color:var(--blue);border:1px solid var(--blue)}
.foot-cols{display:flex;gap:60px;padding-top:46px;font-size:10px;color:var(--muted);letter-spacing:1px}
.subscribe{margin-top:50px;display:flex;justify-content:flex-end;gap:10px;align-items:center}
.subscribe .field{width:240px;height:24px;border-bottom:1px solid var(--line);font-size:10px;color:#aaa;padding-top:6px}
.subscribe .btn{font-size:10px;padding:7px 14px}
.foot-bottom{position:absolute;left:160px;right:160px;bottom:20px;display:flex;justify-content:space-between;font-size:10px;color:var(--muted);border-top:1px solid var(--line);padding-top:18px}
.foot-links{display:flex;gap:40px}
.foot-social{display:flex;gap:18px}
.foot-social span{width:10px;height:10px;border-radius:50%;background:#999}
</style>
</head>
<body>
<header class="site-header">
  <div class="brand"><span class="brand-dot"></span>Plumvessel</div>
  <nav class="main-nav">
    <span>Home</span><span>Founders</span><span class="active">Team</span><span>Advisors</span><span>Careers</span><span>Contact</span>
    <span class="btn btn-green">Login</span><span class="btn btn-blue">Register Now</span>
  </nav>
</header>

<section class="hero">
  <svg width="40" height="40" viewBox="0 0 40 40" aria-hidden="true"><circle cx="20" cy="12" r="7" fill="#fff"/><path d="M6 36c0-9 6-14 14-14s14 5 14 14z" fill="#fff"/></svg>
  <h1>TEAM</h1>
</section>

<div class="crumbs"><span>Home &rsaquo; Team</span><div class="search"><span>Search this</span><span>&#9906;</span></div></div>

<section class="section founders">
  <h2>FOUNDERS</h2>
  <div class="leads">
    <div class="lead"><div class="avatar" role="img" aria-label="Illustrated portrait of John Doe"></div><div><h3>John Doe</h3><p>Guides strategy and client programs, turning vague goals into plans people enjoy.</p><div class="social"><span></span><span></span></div></div></div>
    <div class="lead"><div class="avatar" role="img" aria-label="Illustrated portrait of Alice Doe"></div><div><h3>Alice Doe</h3><p>Runs training and coaching so every mentor and volunteer feels ready from day one.</p><div class="social"><span></span><span></span></div></div></div>
  </div>
  <div class="crew three">
    <div class="mate"><div class="avatar" role="img" aria-label="Illustrated portrait of Craig Murphy"></div><div><h4>Craig Murphy</h4><div class="social"><span></span><span></span></div></div></div>
    <div class="mate"><div class="avatar" role="img" aria-label="Illustrated portrait of Bob Phil"></div><div><h4>Bob Phil</h4><div class="social"><span></span><span></span></div></div></div>
    <div class="mate"><div class="avatar" role="img" aria-label="Illustrated portrait of Helen Price"></div><div><h4>Helen Price</h4><div class="social"><span></span><span></span></div></div></div>
  </div>
</section>

<section class="section members">
  <h2>TEAM MEMBERS</h2>
  <div class="leads">
    <div class="lead"><div class="avatar" role="img" aria-label="Illustrated portrait of John Doe"></div><div><h3>John Doe</h3><p>Builds the tools our customers use to match people, schedule time and track impact.</p><div class="social"><span></span><span></span></div></div></div>
    <div class="lead"><div class="avatar" role="img" aria-label="Illustrated portrait of Alice Doe"></div><div><h3>Alice Doe</h3><p>Designs programs that help employees connect, collaborate and grow across the company.</p><div class="social"><span></span><span></span></div></div></div>
  </div>
  <div class="crew">
    <div class="mate"><div class="avatar" role="img" aria-label="Illustrated portrait of Craig Murphy"></div><div><h4>Craig Murphy</h4><div class="social"><span></span><span></span></div></div></div>
    <div class="mate"><div class="avatar" role="img" aria-label="Illustrated portrait of Bob Phil"></div><div><h4>Bob Phil</h4><div class="social"><span></span><span></span></div></div></div>
    <div class="mate"><div class="avatar" role="img" aria-label="Illustrated portrait of Helen Price"></div><div><h4>Helen Price</h4><div class="social"><span></span><span></span></div></div></div>
    <div class="mate"><div class="avatar" role="img" aria-label="Illustrated portrait of Stephen"></div><div><h4>Stephen</h4><div class="social"><span></span><span></span></div></div></div>
    <div class="mate"><div class="avatar" role="img" aria-label="Illustrated portrait of Craig Paul"></div><div><h4>Craig Paul</h4><div class="social"><span></span><span></span></div></div></div>
    <div class="mate"><div class="avatar" role="img" aria-label="Illustrated portrait of Murphy"></div><div><h4>Murphy</h4><div class="social"><span></span><span></span></div></div></div>
    <div class="mate"><div class="avatar" role="img" aria-label="Illustrated portrait of Mister"></div><div><h4>Mister</h4><div class="social"><span></span><span></span></div></div></div>
    <div class="mate"><div class="avatar" role="img" aria-label="Illustrated portrait of Helen Price"></div><div><h4>Helen Price</h4><div class="social"><span></span><span></span></div></div></div>
  </div>
</section>

<section class="section advisors">
  <h2>ADVISORS</h2>
  <div class="leads">
    <div class="lead"><div class="avatar" role="img" aria-label="Illustrated portrait of John Doe"></div><div><h3>John Doe</h3><p>Advises on growth and partnerships after two decades building enterprise services.</p><div class="social"><span></span><span></span></div></div></div>
  </div>
  <div class="crew two">
    <div class="mate"><div class="avatar" role="img" aria-label="Illustrated portrait of Craig Murphy"></div><div><h4>Craig Murphy</h4><div class="social"><span></span><span></span></div></div></div>
    <div class="mate"><div class="avatar" role="img" aria-label="Illustrated portrait of Bob Phil"></div><div><h4>Bob Phil</h4><div class="social"><span></span><span></span></div></div></div>
  </div>
</section>

<div class="rule"></div>

<section class="clients">
  <h2>A TRACK RECORD OF SUCCESS</h2>
  <div class="client-row">
    <span>Northcove</span><span>Ledgerline</span><span>Halden Systems</span><span>Brackett Motors</span><span>Kindred Fund</span><span>Skyreach Air</span><span>Tallowmark</span>
  </div>
</section>

<footer class="site-footer">
  <div class="foot-top">
    <div class="foot-about">
      <div class="brand"><span class="brand-dot"></span>Plumvessel</div>
      <p>We help organizations launch mentoring, volunteering and collaboration programs that people actually love to join and keep using.</p>
      <span class="btn btn-blue">Request Demo</span><span class="btn btn-outline">Contact Our Team</span>
    </div>
    <div>
      <div class="foot-cols"><span>COMPANY</span><span>ABOUT</span><span>RESOURCES</span></div>
      <div class="subscribe"><div class="field">Your email address</div><span class="btn btn-blue">Subscribe</span></div>
    </div>
  </div>
  <div class="foot-bottom">
    <span>&copy; 2017 Plumvessel Inc. All rights reserved. Plumvessel is a registered trademark of Plumvessel Inc.</span>
    <div class="foot-links"><span>Blog</span><span>Press</span></div>
    <div class="foot-social"><span></span><span></span><span></span></div>
  </div>
</footer>
</body>
</html>
```